KLV Plant Services

We are a heavy diesel mechanical business with additional air con certificates, remapping engine rebuilt

Contact Information for Business Card

Company Name, Director Name, Managing Director, Contact details, email and website

Font styles to use
Serif
Script

```html
<!DOCTYPE html>
<html lang="en">
<head>
<meta charset="utf-8">
<title>KLV Plant Services – Business Card</title>
<link href="https://fonts.googleapis.com/css2?family=Open+Sans:wght@400;700;800&display=swap" rel="stylesheet">
<style>
  :root {
    --backdrop: #3a3431;
    --card: #ffffff;
    --navy: #27246e;
    --ink: #2b2b2b;
    --edge: #2d2a8c;
  }
  * { box-sizing: border-box; margin: 0; padding: 0; }
  html, body {
    width: 1200px; height: 786px; overflow: hidden;
    background: var(--backdrop);
    font-family: "Open Sans", Arial, sans-serif;
  }
  .canvas {
    width: 1200px; height: 786px;
    display: flex; align-items: center; justify-content: center; gap: 44px;
  }
  .card {
    width: 540px; height: 309px;
    background: var(--card);
    position: relative;
    box-shadow: 0 6px 0 var(--edge), 0 14px 30px rgba(0,0,0,.45);
  }

  /* contact side */
  .identity {
    position: absolute; right: 300px; top: 118px;
    text-align: right;
  }
  .identity__name {
    color: var(--navy); font-weight: 700; font-size: 22px; letter-spacing: .5px;
  }
  .identity__role {
    color: var(--navy); font-size: 15px; margin-top: 2px;
  }
  .divider {
    position: absolute; left: 258px; top: 88px;
    width: 2px; height: 96px; background: var(--navy);
  }
  .contacts {
    position: absolute; left: 276px; top: 92px;
    list-style: none; color: var(--ink); font-size: 14.5px; line-height: 1.55;
  }
  .contacts li { display: flex; align-items: center; gap: 8px; }
  .contacts svg { width: 13px; height: 13px; fill: var(--navy); flex: none; }
  .address {
    position: absolute; left: 0; right: 0; bottom: 38px;
    text-align: center; color: var(--ink); font-size: 15px; padding-left: 90px;
  }

  /* brand side */
  .brand {
    position: absolute; inset: 0;
    display: flex; align-items: center; justify-content: center; gap: 16px;
  }
  .brand__dot {
    width: 26px; height: 26px; border-radius: 50%; background: var(--navy);
  }
  .brand__name {
    color: var(--navy); font-weight: 800; font-size: 34px; letter-spacing: .3px;
  }
</style>
</head>
<body>
<main class="canvas">
  <section class="card card--contact">
    <div class="identity">
      <p class="identity__name">DANIEL HART</p>
      <p class="identity__role">Managing Director</p>
    </div>
    <span class="divider"></span>
    <ul class="contacts">
      <li>
        <svg viewBox="0 0 16 16" aria-hidden="true"><path d="M3.6 1.5l2.3 2.6-1.3 1.9c.9 2 2.4 3.5 4.4 4.4l1.9-1.3 2.6 2.3-1.2 2.3C7.3 14.6 1.4 8.7 1.3 2.7z"/></svg>
        123 456 789
      </li>
      <li>
        <svg viewBox="0 0 16 16" aria-hidden="true"><path d="M1 3h14v10H1zm1.6 1.4V5l5.4 3.6L13.4 5v-.6zM2.4 6.6v5h11.2v-5L8 10.3z"/></svg>
        info@yourgmail.com
      </li>
      <li>
        <svg viewBox="0 0 16 16" aria-hidden="true"><path d="M8 1a7 7 0 100 14A7 7 0 008 1zm0 1.5c.9 0 1.9 1.8 2.1 4.6H5.9C6.1 4.3 7.1 2.5 8 2.5zm-5.4 4.6a5.5 5.5 0 012.6-4 9 9 0 00-.8 4zm0 1.8h1.8c.1 1.5.4 2.9.8 4a5.5 5.5 0 01-2.6-4zm3.3 0h4.2c-.2 2.8-1.2 4.6-2.1 4.6s-1.9-1.8-2.1-4.6zm5.7 0h1.8a5.5 5.5 0 01-2.6 4c.4-1.1.7-2.5.8-4zm0-1.8a9 9 0 00-.8-4 5.5 5.5 0 012.6 4z"/></svg>
        www.yourwebsite.com
      </li>
    </ul>
    <p class="address">Your address, City State, Zip 1234</p>
  </section>

  <section class="card card--brand">
    <div class="brand">
      <span class="brand__dot"></span>
      <span class="brand__name">KLV Plant Services</span>
    </div>
  </section>
</main>
</body>
</html>
```